Velvet Lantern rebranding my business with a new business card

I have my new logo and now I need a refresher on my business cards. I really want something fun and fresh. I like black background or anything to make the color pop.
Logo
Name: Velvet Lantern
Contact Info as stated below:
Mira Pellow
555-013-4762
Logo
Name: Velvet Lantern
Mira Pellow
555-013-4762
fb.me/VelvetLanternbyMira
Instagram: @VelvetLanternbyMira

Industry/Entity Type

Business

Contact Information for Business Card

double-sided. Logo on one side. Contact info on the other.

Requirements
Must have
• Logo
• Name: Velvet Lantern
• Contact Info as stated below:
• Mira Pellow
• 555-013-4762
• fb.me/VelvetLanternbyMira
• fb.me/VelvetLanternbyMira

```html
<!DOCTYPE html>
<html lang="en">
<head>
<meta charset="utf-8">
<title>Velvet Lantern – Business Card</title>
<link href="https://fonts.googleapis.com/css2?family=Delius&display=swap" rel="stylesheet">
<style>
  :root {
    --canvas-bg: #e4e4e4;
    --card-white: #fbfbfb;
    --blush: #f4b9bb;
    --blush-soft: #fbd9da;
    --teal: #5cc7b2;
    --ink: #1e1e1e;
    --ring-pink: #e889a0;
    --ring-dark: #2a2a2a;
  }
  * { margin: 0; padding: 0; box-sizing: border-box; }
  html, body { width: 1200px; height: 576px; overflow: hidden; }
  body {
    position: relative;
    background: var(--canvas-bg);
    font-family: "Delius", "Comic Neue", sans-serif;
    color: var(--ink);
  }
  .card {
    position: absolute;
    top: 138px;
    width: 482px;
    height: 292px;
    border-radius: 13px;
    overflow: hidden;
  }
  .card--front { left: 82px; background: var(--blush); }
  .card--back { left: 602px; background: var(--card-white); }

  .logo-badge {
    position: absolute;
    left: 138px;
    top: 44px;
    width: 206px;
    height: 206px;
    border-radius: 50%;
    background: var(--card-white);
    border: 2px solid var(--ring-dark);
    box-shadow: inset 0 0 0 5px var(--card-white), inset 0 0 0 6px var(--ring-pink);
    display: flex;
    align-items: center;
    justify-content: center;
  }
  .brand-name {
    font-family: "Delius", "Comic Neue", sans-serif;
    font-weight: 400;
    color: var(--ink);
    text-align: center;
    line-height: 1.1;
  }
  .logo-badge .brand-name { font-size: 26px; }

  .wave { position: absolute; inset: 0; }

  .card-logo {
    position: absolute;
    left: 18px;
    top: 90px;
    width: 212px;
    height: 160px;
    display: flex;
    align-items: center;
    justify-content: center;
  }
  .card-logo .brand-name { font-size: 32px; }

  .holder {
    position: absolute;
    right: 26px;
    top: 24px;
    text-align: right;
  }
  .holder-name { font-size: 24px; line-height: 1.2; }
  .holder-title { font-size: 11px; margin-top: 1px; }

  .contact {
    position: absolute;
    right: 26px;
    top: 200px;
    list-style: none;
    font-size: 18px;
  }
  .contact li {
    display: flex;
    align-items: center;
    justify-content: flex-end;
    gap: 7px;
    height: 27px;
  }
  .contact-icon {
    width: 17px;
    height: 17px;
    border: 1.5px solid var(--ink);
    border-radius: 4px;
    display: flex;
    align-items: center;
    justify-content: center;
    flex: none;
  }
</style>
</head>
<body>

  <section class="card card--front" aria-label="Card front">
    <div class="logo-badge">
      <span class="brand-name">Velvet<br>Lantern</span>
    </div>
  </section>

  <section class="card card--back" aria-label="Card back">
    <svg class="wave" viewBox="0 0 482 292" preserveAspectRatio="none" aria-hidden="true">
      <path d="M0 0 H482 V144 C400 130 320 60 200 30 C120 12 60 14 0 22 Z" fill="var(--blush-soft)"/>
      <path d="M0 30 C70 20 140 24 220 50 C320 84 400 140 482 138 V152 C400 156 320 104 220 70 C140 44 70 40 0 52 Z" fill="var(--teal)"/>
    </svg>

    <div class="card-logo">
      <span class="brand-name">Velvet<br>Lantern</span>
    </div>

    <div class="holder">
      <p class="holder-name">Mira Pellow</p>
      <p class="holder-title">Managing Director</p>
    </div>

    <ul class="contact">
      <li>
        <span>555-013-4762</span>
        <span class="contact-icon">
          <svg width="11" height="11" viewBox="0 0 24 24" aria-hidden="true"><path d="M6.6 10.8a15.1 15.1 0 0 0 6.6 6.6l2.2-2.2a1 1 0 0 1 1-.25 11.4 11.4 0 0 0 3.6.57 1 1 0 0 1 1 1V20a1 1 0 0 1-1 1A17 17 0 0 1 3 4a1 1 0 0 1 1-1h3.5a1 1 0 0 1 1 1c0 1.25.2 2.45.57 3.57a1 1 0 0 1-.25 1z" fill="var(--ink)"/></svg>
        </span>
      </li>
      <li>
        <span>VelvetLanternbyMira</span>
        <span class="contact-icon"></span>
      </li>
    </ul>
  </section>

</body>
</html>
```